PillPeak website blog. Simple medical advice given in clear yes or no answers that save people money

I am developing a new web page that provides medical care cost savings at the consumers' fingertips. I need a web page that is clean, concise, and attractive for me to put my valuable medical information on. The information I provide is simple to obtain, yet very valuable to the consumer, and answered in a yes or no format. For example, A person may wonder if they need an antibiotic for cold like symptoms. Seeing a doctor for an antibiotic is very expensive. But with simple and clear advice at their fingertips, they can confidently avoid having to pay $200 or more to see a doctor and get an antibiotic. This is kind of like consumer reports for medical services.

Target Market(s)

People who are savvy shoppers and want to save money on healthcare. Likely younger ages between 21 and 60, who are mobile, readily use iphones, and want strong evidence based research to guide their decisions.

Industry/Entity Type

Coding

Number of Pages Required

Colors

Requirements
Must have
• A template on the "Question" and "Answer" page that can be edited many times that can be edited many times. The Confidence rating scale would need to be edited as well. The "Date Researched" the "PillPeak Pilluminate" and "References" all need to be able to be edited. This website must be very clear and simple to understand. A medical question is posed with a yes or no answer, then answered and given a confidence rating, we then tell them how much money they saved by going to our website.
Nice to have
• We want this to be slightly fun, vibrant, warm and inviting. This will be sometime later converted into an app format. Quirky, some humor to keep it interesting.
Should not have
• No sterile looking medical images. Not boring.

```html
<!DOCTYPE html>
<html lang="en">
<head>
<meta charset="utf-8">
<title>PillPeak</title>
<link href="https://fonts.googleapis.com/css2?family=Montserrat:wght@400;500;700&family=Open+Sans:wght@400;600;700&family=Rubik:wght@700;900&display=swap" rel="stylesheet">
<style>
:root{
  --blue:#1565b4;
  --blue-light:#2b7cc9;
  --red:#e0202b;
  --ink:#111;
  --white:#fff;
  --panel:rgba(18,18,20,.94);
  --rule:rgba(255,255,255,.12);
}
*{margin:0;padding:0;box-sizing:border-box}
html,body{width:1200px;height:1168px;overflow:hidden;background:var(--white)}
body{position:relative;font-family:'Montserrat',sans-serif;color:var(--ink)}
.site-header{position:absolute;left:0;top:0;width:1200px;height:158px}
.brand{position:absolute;left:146px;top:62px;display:flex;align-items:center;gap:10px}
.brand-dot{width:30px;height:30px;border-radius:50%;background:var(--blue)}
.brand-name{font-family:'Rubik',sans-serif;font-weight:700;font-size:36px;color:var(--red)}
.search{position:absolute;left:760px;top:29px;width:297px;height:41px;border:2px solid #c9c9c9;display:flex;align-items:center;padding:0 17px;font-size:11px;letter-spacing:.3px;color:#333}
.search svg{position:absolute;right:14px;top:12px}
.tagline{position:absolute;left:489px;top:103px;width:568px;font-size:22.5px;display:flex;justify-content:space-between;white-space:nowrap}
.tagline b{font-weight:700}
.main-nav{position:absolute;left:0;top:158px;width:1200px;height:37px;background:var(--blue)}
.main-nav ul{list-style:none;position:relative;height:100%}
.main-nav li{position:absolute;top:0;line-height:37px;color:var(--white);font-weight:700;font-size:12px}
.hero{position:absolute;left:0;top:195px;width:1200px;height:593px;background:radial-gradient(ellipse at 58% 45%,#8a9aa8 0%,#5b6f80 30%,#34434f 60%,#1a2128 100%)}
.side-menu{position:absolute;left:19px;top:92px;width:283px;height:391px;background:var(--panel);list-style:none;padding-top:6px}
.side-menu li{margin:0 33px 0 27px;height:51px;line-height:51px;padding-left:15px;font-size:16px;color:var(--white);border-bottom:1px solid var(--rule)}
.side-menu li:last-child{border-bottom:none}
.hero-headline{position:absolute;left:822px;top:275px;font-family:'Rubik',sans-serif;font-weight:900;font-size:35px;line-height:40px;color:var(--white)}
.slider-dots{position:absolute;top:533px;left:0;width:100%;height:14px}
.slider-dots span{position:absolute;top:3px;width:9px;height:9px;border-radius:50%;background:var(--white)}
.slider-dots span.active{top:0;width:14px;height:14px;background:transparent;border:2px solid var(--white)}
.site-footer{position:absolute;left:0;top:788px;width:1200px;height:380px;background:var(--blue);color:var(--white)}
.footer-heading{position:absolute;top:64px;font-family:'Rubik',sans-serif;font-weight:700;font-size:21px}
.disclaimer-text{position:absolute;left:145px;top:118px;width:450px;font-family:'Open Sans',sans-serif;font-size:12.2px;line-height:16px}
.signup{position:absolute;left:682px;top:111px;width:375px;height:43px;background:var(--white);display:flex;align-items:center;padding-left:19px;font-size:12px;color:#333}
.signup-btn{position:absolute;right:10px;top:7px;width:37px;height:29px;background:var(--red);display:flex;align-items:center;justify-content:center}
.ask-box{position:absolute;left:682px;top:172px;width:374px;height:74px;background:var(--blue-light);padding:16px 0 0 33px;font-family:'Open Sans',sans-serif;font-weight:700;font-size:14.5px;line-height:20px}
.footer-rule{position:absolute;left:145px;top:300px;width:910px;height:1px;background:rgba(255,255,255,.3)}
.copyright{position:absolute;top:334px;width:100%;text-align:center;font-family:'Open Sans',sans-serif;font-size:12px}
</style>
</head>
<body>
<header class="site-header">
  <div class="brand"><span class="brand-dot"></span><span class="brand-name">PillPeak</span></div>
  <div class="search">SEARCH
    <svg width="16" height="16" viewBox="0 0 16 16"><circle cx="6.5" cy="6.5" r="5" fill="none" stroke="#999" stroke-width="2"/><line x1="10.2" y1="10.2" x2="14.5" y2="14.5" stroke="#999" stroke-width="2.2"/></svg>
  </div>
  <div class="tagline"><span>CLEAR VALUABLE.</span><b>HEALTH ADVICE.</b><span>RIGHT NOW</span></div>
</header>
<nav class="main-nav">
  <ul>
    <li style="left:146px">PREV/SCREENING</li>
    <li style="left:303px">WOMEN'S HEALTH</li>
    <li style="left:468px">MEN'S HEALTH</li>
    <li style="left:606px">MEDS</li>
    <li style="left:695px">SURGERY</li>
    <li style="left:802px">IMAGING</li>
    <li style="left:909px">PEDS</li>
    <li style="left:978px">CONTACT US</li>
  </ul>
</nav>
<section class="hero" role="img" aria-label="Photo of a gloved hand framing a glowing holographic scan of a head and spine in front of a surgeon">
  <ul class="side-menu">
    <li>Who are We?</li>
    <li>How it Works</li>
    <li>How we Know</li>
    <li>Evidence based Research</li>
    <li>Dr. Whitfield</li>
    <li>Who we are not</li>
    <li>Are we biased?</li>
  </ul>
  <h1 class="hero-headline">Save $1000 Per<br>Year on Healthcare.<br>It's Free!</h1>
  <div class="slider-dots">
    <span style="left:544px"></span><span style="left:566px"></span><span class="active" style="left:590px"></span><span style="left:616px"></span><span style="left:647px"></span>
  </div>
</section>
<footer class="site-footer">
  <h2 class="footer-heading" style="left:145px">Disclaimer</h2>
  <p class="disclaimer-text">Sed ut perspiciatis unde omnis iste natus error sit voluptatem accusantium doloremque laudantium, totam rem aperiam, eaque ipsa quae ab illo inventore veritatis et quasi architecto beatae vitae dicta sunt explicabo. Nemo enim ipsam voluptatem quia voluptas sit aspernatur aut odit aut fugit, sed quia conseq uuntur magni dolores eos qui ratione voluptatem sequi nesciunt. Neque porro quisquam est, qui dolorem ipsum quia dolor sit amet, consectetur, adipisci velit, sed quia non numquam eius.</p>
  <h2 class="footer-heading" style="left:679px">Become a Pill Peak Today!</h2>
  <div class="signup">Enter Email
    <span class="signup-btn"><svg width="15" height="11" viewBox="0 0 15 11"><rect width="15" height="11" rx="1" fill="#fff"/><path d="M0.5 1 L7.5 6 L14.5 1" fill="none" stroke="#e0202b" stroke-width="1.5"/></svg></span>
  </div>
  <div class="ask-box">Ask a Question here!<br>If it is worthy well post it!</div>
  <div class="footer-rule"></div>
  <p class="copyright">Copyrights @ 2018 All Rights Reserved</p>
</footer>
</body>
</html>
```